Life Coaching business needs a new flyer

We are an Australian business that specialises in Life Coaching, Career Coaching, Health and Wellness Coaching, Yoga and Pilates. We need a A4 double sided flyer that is full colour and folded to DL format. I have attached a couple of designs that I like and some pictures and would like the flyer to be bright yet stylish.

Industry/Entity Type

Life Coaching

```html
<!DOCTYPE html>
<html lang="en">
<head>
<meta charset="utf-8">
<title>Life Coaching and Meditation Centre of Excellence – Trifold</title>
<link rel="stylesheet" href="https://fonts.googleapis.com/css2?family=Open+Sans:ital,wght@0,400;0,600;0,700;1,600;1,700&display=swap">
<style>
  :root {
    --page-bg: #e6e6e6;
    --paper: #ffffff;
    --blue: #1f7dc2;
    --blue-dark: #135f9e;
    --green: #5aaa2e;
    --text: #5b6670;
    --sky-top: #2d86c8;
    --sky-low: #a9d3ee;
    --grass: #6ea33a;
  }
  * { margin: 0; padding: 0; box-sizing: border-box; }
  html, body { width: 1200px; height: 870px; overflow: hidden; }
  body {
    background: var(--page-bg);
    font-family: "Open Sans", Arial, sans-serif;
    color: var(--text);
  }
  .brochure {
    position: absolute;
    left: 20px; top: 25px;
    width: 1160px; height: 820px;
    display: flex;
    background: var(--paper);
    box-shadow: 0 6px 22px rgba(0,0,0,.18);
  }
  .panel {
    position: relative;
    width: 386.67px; height: 820px;
    overflow: hidden;
  }
  .panel + .panel { border-left: 1px solid rgba(0,0,0,.06); }
  .panel-art { position: absolute; inset: 0; width: 100%; height: 100%; }
  .copy { position: absolute; font-size: 11.5px; line-height: 1.45; }
  .section-title {
    color: var(--blue);
    font-weight: 600;
    font-size: 17px;
    line-height: 1.2;
    margin-bottom: 3px;
  }
  .section-title.green { color: var(--green); }
  .copy p { text-align: justify; }
  .copy p + .section-title { margin-top: 14px; }
  .tick-list { list-style: none; }
  .tick-list li {
    position: relative;
    padding-left: 17px;
    margin-bottom: 4px;
  }
  .tick-list li::before {
    content: "";
    position: absolute;
    left: 0; top: 4px;
    width: 10px; height: 10px;
    border-radius: 50%;
    background: var(--green);
  }
  .tick-list li::after {
    content: "";
    position: absolute;
    left: 3px; top: 7px;
    width: 3px; height: 3px;
    border-right: 1.5px solid #fff;
    border-bottom: 1.5px solid #fff;
    transform: rotate(-45deg);
  }
  .tick-list.compact li { margin-bottom: 1px; }
  .intro { left: 30px; top: 32px; width: 330px; font-size: 12px; }
  .answer {
    color: var(--green);
    font-style: italic;
    font-weight: 700;
    font-size: 16px;
    margin-top: 14px;
  }
  .centre-title {
    color: var(--blue);
    font-weight: 600;
    font-size: 19px;
    line-height: 1.2;
    margin-bottom: 8px;
  }
  .mission { left: 30px; top: 615px; width: 330px; font-size: 12px; }
  .brand-badge {
    position: absolute;
    left: 238px; top: 470px;
    width: 100px; height: 100px;
    border-radius: 50%;
    background: var(--paper);
    box-shadow: 0 2px 8px rgba(0,0,0,.25);
    display: flex; align-items: center; justify-content: center;
    text-align: center;
    color: var(--blue);
    font-weight: 600;
    font-size: 12px;
    line-height: 1.25;
  }
  .services { left: 30px; top: 248px; width: 330px; }
  .help { left: 30px; top: 28px; width: 330px; }
  .practice { left: 30px; top: 652px; width: 330px; }
</style>
</head>
<body>
<main class="brochure">

  <section class="panel panel-welcome">
    <svg class="panel-art" viewBox="0 0 387 820" preserveAspectRatio="none">
      <defs>
        <linearGradient id="tint1" x1="0" y1="0" x2="0" y2="1">
          <stop offset="0" stop-color="#ffffff"/><stop offset="1" stop-color="#d7eaf7"/>
        </linearGradient>
        <linearGradient id="boat" x1="0" y1="0" x2="0" y2="1">
          <stop offset="0" stop-color="#2f7fc4"/><stop offset=".55" stop-color="#4f98d2"/><stop offset="1" stop-color="#1c4f86"/>
        </linearGradient>
      </defs>
      <rect role="img" aria-label="Photo: smiling older couple sitting on the bow of a white sailing boat on a calm blue sea" x="0" y="220" width="387" height="400" fill="url(#boat)"/>
      <path d="M0 0H387V225C270 228 150 250 0 300Z" fill="url(#tint1)"/>
      <path d="M0 300C150 250 270 228 387 225V246C270 250 150 272 0 328Z" fill="var(--green)"/>
      <path d="M0 328C150 272 270 250 387 246V252C270 256 150 280 0 338Z" fill="#ffffff"/>
      <path d="M0 595C120 535 260 515 387 522V820H0Z" fill="url(#tint1)"/>
      <path d="M0 575C120 515 260 495 387 502V522C260 515 120 535 0 595Z" fill="var(--blue)"/>
    </svg>
    <div class="copy intro">
      <ul class="tick-list">
        <li>Are you looking at making changes this year?</li>
        <li>Are you stuck in a rut or at a crossroad in your life?</li>
        <li>Are you wanting to lose weight but can't get motivated?</li>
        <li>Do you have ongoing problems with your career, relationships, or just life itself?</li>
      </ul>
      <p class="answer">Life coaching is the answer!</p>
    </div>
    <div class="brand-badge">Clearwater<br>Coaching</div>
    <div class="copy mission">
      <h1 class="centre-title">Life Coaching and Meditation<br>Centre of Excellence</h1>
      <p>Our mission is to help you become the best possible person you can be. Mentally, physically, and spiritually. We offer highly qualified and compassionate trainers/coaches for Life Coaching, Meditation, Yoga and Pilates. They will guide and motivate you every step of the way to achieve all your dreams and goals. They will make you be the best you can be!</p>
    </div>
  </section>

  <section class="panel panel-services">
    <svg class="panel-art" viewBox="0 0 387 820" preserveAspectRatio="none">
      <defs>
        <linearGradient id="sky2" x1="0" y1="0" x2="0" y2="1">
          <stop offset="0" stop-color="var(--sky-top)"/><stop offset=".7" stop-color="var(--sky-low)"/><stop offset="1" stop-color="#e9f4fb"/>
        </linearGradient>
        <linearGradient id="field" x1="0" y1="0" x2="0" y2="1">
          <stop offset="0" stop-color="#7fb8e6"/><stop offset=".35" stop-color="#5a8fc0"/><stop offset=".5" stop-color="var(--grass)"/><stop offset="1" stop-color="#4f8a25"/>
        </linearGradient>
      </defs>
      <rect role="img" aria-label="Photo: woman in white holding a balancing yoga pose on a beach under a blue sky" x="0" y="0" width="387" height="250" fill="url(#sky2)"/>
      <path d="M0 255C120 215 260 205 387 225V820H0Z" fill="#ffffff"/>
      <path d="M0 238C120 198 260 188 387 208V225C260 205 120 215 0 255Z" fill="var(--green)"/>
      <rect role="img" aria-label="Photo: group of people in colourful clothes meditating cross-legged on yoga mats on a lawn by the water" x="0" y="695" width="387" height="125" fill="url(#field)"/>
      <path d="M0 660H387V700C270 727 140 740 0 720Z" fill="#ffffff"/>
      <path d="M0 720C140 740 270 727 387 700V712C270 739 140 752 0 732Z" fill="var(--blue)"/>
    </svg>
    <div class="copy services">
      <h2 class="section-title">Life Coaching</h2>
      <p>Your Life Coach will give you the confidence and the ability to move forward in a positive manner in all areas of your life where you crave change. Life Coaching is about breaking down the barriers preventing this change from happening, and creating the ideal environment for positive action to take place. It is a holistic approach, which looks at the present and sets goals for a totally successful future.</p>
      <h2 class="section-title">Career Coaching</h2>
      <p>Are you at a crossroads in your career and at a loss about what to do next? Do you want your work to be in alignment with the authentic you? It can be difficult to assess career options, goals, and strategies, and have the confidence to implement changes on your own. With the right coaching support, you will gain the clarity that you need to take control and have a fulfilling and rewarding career.</p>
      <h2 class="section-title">Wellness Coaching</h2>
      <p>Health and wellness coaches help their clients find the motivation and tools to achieve their health and wellness goals, working with the client to examine and improve the psychological framework that supports those goals.</p>
    </div>
  </section>

  <section class="panel panel-practice">
    <svg class="panel-art" viewBox="0 0 387 820" preserveAspectRatio="none">
      <defs>
        <linearGradient id="tint3" x1="0" y1="0" x2="0" y2="1">
          <stop offset="0" stop-color="#eef6fb"/><stop offset="1" stop-color="#d4e8f5"/>
        </linearGradient>
        <linearGradient id="beach" x1="0" y1="0" x2="0" y2="1">
          <stop offset="0" stop-color="#8ec4e8"/><stop offset=".6" stop-color="#cfe6f4"/><stop offset="1" stop-color="#a8cbe0"/>
        </linearGradient>
      </defs>
      <rect role="img" aria-label="Photo: man and woman in white standing in tree pose with arms raised on a misty beach" x="0" y="300" width="387" height="330" fill="url(#beach)"/>
      <path d="M0 0H387V290C280 305 150 315 0 325Z" fill="url(#tint3)"/>
      <path d="M0 325C150 315 280 305 387 290V310C280 327 150 337 0 345Z" fill="var(--blue)"/>
      <path d="M0 618C130 580 270 540 387 495V820H0Z" fill="url(#tint3)"/>
      <path d="M0 600C130 560 270 520 387 475V495C270 540 130 580 0 618Z" fill="var(--green)"/>
      <path d="M0 618C130 580 270 540 387 495V505C270 552 130 592 0 628Z" fill="var(--blue-dark)"/>
    </svg>
    <div class="copy help">
      <h2 class="section-title green">Why Would I Need Help?</h2>
      <p>Coaching is for anyone who wants to make lasting changes in their life.</p>
      <p style="margin:4px 0 6px">Coaching can assist with such issues as:</p>
      <ul class="tick-list compact">
        <li>Creating a better work - life balance</li>
        <li>Resolving relationship issues</li>
        <li>Career guidance</li>
        <li>Stress management</li>
        <li>Weight loss and fitness</li>
        <li>Motivation and goal setting</li>
        <li>Boosting your self esteem</li>
        <li>Overcoming negative emotions and thoughts</li>
        <li>Better time management</li>
      </ul>
    </div>
    <div class="copy practice">
      <h2 class="section-title">Meditation</h2>
      <p>We specialise in teaching meditation from beginners to advanced and teach a variety of techniques for stress reduction, peace of mind, stillness, and clarity.</p>
      <h2 class="section-title">Yoga/Pilates</h2>
      <p>Your highly qualified and experienced Yoga or Pilates instructor will come to you and create a fun and varied workout based on what you enjoy and what your goals are.</p>
    </div>
  </section>

</main>
</body>
</html>
```